Business cards to launch an education platform

Hi,
I am looking at having new business cards designed.
I am a startup, developing a web platform for schools and university, the education world. It's an online assessment system.
I would like a card that looks classy, and that is using the colors and the font of my logo.

I have attached:
1) my logo
2) A business card that I have designed quickly so you can have all the information required in the card, but I really don't like it.
3) The font that I am using (Lato Regular) to design my web platform
4) Some screenshots of my web platform so you can have a look at the style that I have.

Target Market(s)

Major market: Education system: Schools and university
Minor markets: Business in general

Industry/Entity Type

Business

Contact Information for Business Card

Clara Fenwick
Director

M: 0437 518 902
E: clara.fenwick@amberLoomSystems.com.au

Requirements
Must have
• The colors of my logo

```html
<!DOCTYPE html>
<html lang="en">
<head>
<meta charset="UTF-8">
<title>Amber Loom Systems – Business Card</title>
<link rel="stylesheet" href="https://fonts.googleapis.com/css2?family=Lato:wght@400;700&display=swap">
<style>
  :root {
    --page-bg: #e4e4e4;
    --card-black: #050505;
    --blue-light: #2fb0e0;
    --blue-mid: #1f8fd2;
    --blue-deep: #1470c0;
    --brand-blue: #2a8fd6;
    --swoosh-dark: #1b5fa8;
    --text-white: #ffffff;
  }
  * { margin: 0; padding: 0; box-sizing: border-box; }
  html, body {
    width: 1200px; height: 900px; overflow: hidden;
    background: var(--page-bg);
    font-family: "Lato", sans-serif;
  }
  .sheet {
    width: 1200px; height: 900px;
    display: flex; flex-direction: column;
    align-items: center; justify-content: center; gap: 48px;
  }
  .card {
    position: relative;
    width: 640px; height: 366px;
    overflow: hidden;
    box-shadow: 0 6px 18px rgba(0,0,0,0.18);
  }
  .card-back {
    background: var(--card-black);
    display: flex; align-items: center; justify-content: center;
  }
  .back-brand {
    display: flex; align-items: center; gap: 18px;
    color: var(--text-white);
    font-size: 34px; font-weight: 700; letter-spacing: 3px;
    text-transform: uppercase;
  }
  .back-brand .brand-square {
    width: 54px; height: 54px; background: var(--text-white);
  }
  .card-front .front-bg {
    position: absolute; inset: 0; width: 100%; height: 100%;
  }
  .front-brand {
    position: absolute; left: 190px; top: 58px;
    display: flex; align-items: center; gap: 14px;
    color: var(--brand-blue);
    font-weight: 400;
  }
  .front-brand .brand-square {
    width: 56px; height: 56px; background: var(--brand-blue);
  }
  .front-brand .brand-name {
    font-size: 27px; line-height: 1.05; letter-spacing: 3px;
    text-transform: uppercase;
  }
  .contact {
    position: absolute; left: 0; right: 0; top: 208px;
    text-align: center; color: var(--text-white);
  }
  .contact .person-name { font-size: 23px; font-weight: 700; }
  .contact .person-role { font-size: 14px; margin-top: 1px; }
  .contact .line {
    display: flex; align-items: center; justify-content: center; gap: 8px;
    font-size: 16px; margin-top: 10px;
  }
  .contact .line + .line { margin-top: 6px; font-size: 15px; }
  .contact .icon { width: 13px; height: 13px; fill: var(--text-white); }
</style>
</head>
<body>
<main class="sheet">

  <section class="card card-back" aria-label="Card back">
    <div class="back-brand">
      <span class="brand-square"></span>
      <span class="brand-name">Amber Loom Systems</span>
    </div>
  </section>

  <section class="card card-front" aria-label="Card front">
    <svg class="front-bg" viewBox="0 0 640 366" preserveAspectRatio="none" aria-hidden="true">
      <defs>
        <linearGradient id="blueField" x1="0" y1="0" x2="0.3" y2="1">
          <stop offset="0" stop-color="var(--blue-light)"/>
          <stop offset="0.55" stop-color="var(--blue-mid)"/>
          <stop offset="1" stop-color="var(--blue-deep)"/>
        </linearGradient>
        <linearGradient id="swoosh" x1="0" y1="0" x2="1" y2="0">
          <stop offset="0" stop-color="var(--blue-light)"/>
          <stop offset="1" stop-color="var(--swoosh-dark)"/>
        </linearGradient>
      </defs>
      <rect class="blue-field" width="640" height="366" fill="url(#blueField)"/>
      <path class="black-field" d="M0 0 H640 V178 C520 196 360 196 250 178 C150 160 60 120 0 84 Z" fill="var(--card-black)"/>
      <path class="swoosh-band" d="M0 66 C90 120 200 160 330 182 C220 150 110 110 0 54 Z" fill="url(#swoosh)"/>
      <path class="swoosh-thin" d="M0 94 C120 150 260 186 420 192 C270 180 140 146 0 86 Z" fill="var(--blue-light)" opacity="0.85"/>
      <path class="swoosh-edge" d="M250 178 C360 196 520 196 640 178 V186 C520 204 360 204 250 186 Z" fill="var(--swoosh-dark)"/>
    </svg>

    <div class="front-brand">
      <span class="brand-square"></span>
      <span class="brand-name">Amber Loom<br>Systems</span>
    </div>

    <div class="contact">
      <p class="person-name">Clara Fenwick</p>
      <p class="person-role">Director</p>
      <p class="line">
        <svg class="icon" viewBox="0 0 24 24" aria-hidden="true"><path d="M6.6 10.8a15.1 15.1 0 0 0 6.6 6.6l2.2-2.2a1 1 0 0 1 1-.25 11.4 11.4 0 0 0 3.6.57 1 1 0 0 1 1 1V20a1 1 0 0 1-1 1A17 17 0 0 1 3 4a1 1 0 0 1 1-1h3.5a1 1 0 0 1 1 1c0 1.25.2 2.45.57 3.57a1 1 0 0 1-.25 1z"/></svg>
        <span>0437 518 902</span>
      </p>
      <p class="line">
        <svg class="icon" viewBox="0 0 24 24" aria-hidden="true"><path d="M2 5h20v14H2z M4 7v.5l8 5 8-5V7l-8 5z" fill-rule="evenodd"/></svg>
        <span>clara.fenwick@amberLoomSystems.com.au</span>
      </p>
    </div>
  </section>

</main>
</body>
</html>
```